Destination PDF Template (Editable)

Objective: Create a visually stunning and compelling PDF brochure that showcases The Vorelka Crest Lodge as the ultimate luxury hunting destination in Kyrgyzstan, specializing in Marco Polo and Ibex hunts. The PDF should evoke a sense of exclusivity, adventure, and the breathtaking beauty of the Tian Shan mountains, ultimately driving bookings.
Target Audience: High-net-worth individuals, discerning hunters seeking exceptional experiences, adventure travelers, and those interested in unique and luxurious wilderness experiences.
Overall Tone & Style: Sophisticated, elegant, and aspirational. Think high-end travel magazines combined with a touch of rugged adventure. Avoid anything that feels generic or overly commercial. The design should reflect the unparalleled nature of the lodge and the hunts offered. (I'm attaching a reference PDF that i like), as well as another instructions file. Drive link for photos: https://files.pondery-share.net/box/folders/7KqLm2xVbR4tWz9hN3cJpE6yF0aDs8uG?mode=open
Another Link: https://files.pondery-share.net/box/u/0/folders/9ZtRe4wQmN2bVx7kLp5sHc8jYd3fGa1oU

```html
<!DOCTYPE html>
<html lang="en">
<head>
<meta charset="utf-8">
<title>The Vorelka Crest Lodge – Kyrgyzstan 2025</title>
<link rel="stylesheet" href="https://fonts.googleapis.com/css2?family=League+Spartan:wght@600;700;800&family=Carlito:wght@400;700&display=swap">
<style>
:root{
  --backdrop:#8c8c8c;
  --paper:#ffffff;
  --ink:#111111;
  --accent:#a3263a;
  --muted:#444444;
  --badge:#222222;
  --pin:#d8322c;
}
*{margin:0;padding:0;box-sizing:border-box}
html,body{width:1200px;height:4978px;overflow:hidden}
body{background:var(--backdrop);font-family:"Carlito",sans-serif;color:var(--ink);position:relative}
.page{position:absolute;left:369px;width:460px;height:650px;background:var(--paper);overflow:hidden}
.abs{position:absolute}
.photo{position:absolute;overflow:hidden}
.heading{font-family:"League Spartan",sans-serif;font-weight:800;letter-spacing:.5px;white-space:nowrap}
.label{font-family:"League Spartan",sans-serif;font-weight:700;font-size:12px;letter-spacing:.3px}
.red{color:var(--accent)}
.small{font-size:7px;line-height:1.22;font-weight:700}
.body{font-size:9px;line-height:1.3}
.list{font-size:9.5px;line-height:1.55}
.caption{color:#fff;font-size:10px;line-height:1.25}
.brand-name{font-family:"League Spartan",sans-serif;font-weight:700;white-space:nowrap}

/* photo tone fields */
.tone-cover{background:linear-gradient(172deg,#4f78b0 0%,#8fa9c8 18%,#d6dbe2 30%,#8c8a88 42%,#9b7b5c 60%,#7a5a3f 78%,#3d2c20 100%)}
.tone-sunset-ram{background:linear-gradient(180deg,#2e3a55 0%,#5a6585 14%,#d9a39a 26%,#f0d6cc 34%,#b8c0cc 48%,#eef0f3 62%,#6e7078 80%,#2a2a2e 100%)}
.tone-riders-valley{background:linear-gradient(180deg,#bfc6cf 0%,#dfe2e6 30%,#9a9890 52%,#b08a4e 72%,#6f5126 100%)}
.tone-range{background:linear-gradient(180deg,#cdd5de 0%,#9aa4ae 25%,#6a6460 50%,#8a7358 72%,#a07f55 100%)}
.tone-map{background:linear-gradient(100deg,#e4e3df 0%,#cfcdc6 30%,#c9b08a 55%,#d4b88f 100%)}
.tone-stream{background:linear-gradient(180deg,#8a7a64 0%,#a08a66 35%,#6b5a44 65%,#7f8a8c 100%)}
.tone-white-horse{background:linear-gradient(180deg,#c5c9ce 0%,#8d8883 30%,#6a625c 55%,#d8d6d2 72%,#4a4240 100%)}
.tone-horses-rest{background:linear-gradient(180deg,#b6bcc2 0%,#8f918a 30%,#6b7548 60%,#4a4a3a 100%)}
.tone-prone{background:linear-gradient(180deg,#b4c3d2 0%,#dde2e7 38%,#56667a 60%,#2f3a48 78%,#9a8464 100%)}
.tone-lounge{background:radial-gradient(ellipse at 50% 20%,#f0c27a 0%,#b8823f 35%,#6e4522 70%,#3a2414 100%)}
.tone-sitting{background:linear-gradient(180deg,#8c4e1e 0%,#b97a3e 40%,#c89a68 62%,#e6ded2 82%,#b7a58e 100%)}
.tone-dining{background:radial-gradient(ellipse at 50% 30%,#b08458 0%,#7a5230 45%,#4a2e1c 100%)}
.tone-billiards{background:linear-gradient(180deg,#2e2016 0%,#6a4a2c 35%,#8a6a44 50%,#1f9a8c 66%,#187a70 82%,#3a2a1e 100%)}
.tone-corridor{background:radial-gradient(ellipse at 50% 45%,#e8d6b0 0%,#b07a40 25%,#6a4222 60%,#2e1c10 100%)}

/* cover */
.cover-title{top:22px;left:0;width:100%;text-align:center;font-size:25px}
.cover-photo{top:70px;left:29px;width:402px;height:537px}
.cover-brand{position:absolute;top:40px;font-size:8px;color:#fff}
.cover-badge{top:628px;left:166px;width:128px;height:20px;background:var(--badge);color:#fff;font-family:"League Spartan",sans-serif;font-weight:700;font-size:11px;text-align:center;line-height:21px}

/* hunt details */
.hero{top:19px;left:19px;width:421px;height:193px}
.hero-title{position:absolute;bottom:6px;width:100%;text-align:center;color:#fff;font-size:27px}
</style>
</head>
<body>

<!-- Cover -->
<section class="page" style="top:110px">
  <h1 class="heading abs cover-title">THE VORELKA CREST LODGE</h1>
  <div class="photo cover-photo tone-cover" role="img" aria-label="Two hunters in winter gear kneeling behind a Marco Polo ram on a rocky Tian Shan slope, snow peaks behind">
    <span class="brand-name cover-brand" style="left:14px">TRAILMARK</span>
    <span class="brand-name cover-brand" style="right:14px">RIDGELINE WORKS</span>
  </div>
  <div class="abs cover-badge">KYRGYZSTAN 2025</div>
</section>

<!-- A Hunter's Paradise -->
<section class="page" style="top:794px">
  <h2 class="heading abs red" style="top:30px;left:36px;font-size:29px">A HUNTER'S PARADISE:</h2>
  <p class="abs" style="top:61px;left:36px;font-size:22px">Where Luxury Roams Free</p>
  <p class="abs body" style="top:100px;left:36px;width:390px;color:var(--muted)">Renowned as one of the Best Mountain Hunting Lodges in the World, this Kyrgyzstan camp offers adventure and luxury in the majestic Tian Shan Mountains. Hunt Marco Polo sheep and Ibex across rugged terrain, then relax in unparalleled comfort. Unwind in this secluded oasis, surrounded by breathtaking panoramas of the Kyrgyz landscape. This is where the adventure of the hunt seamlessly blends with the comforts of an unparalleled wilderness retreat.</p>
  <div class="photo tone-sunset-ram" style="top:182px;left:33px;width:392px;height:268px" role="img" aria-label="Hunter seated in snow beside a Marco Polo ram at sunset with pink mountain peaks"></div>
  <div class="photo tone-riders-valley" style="top:471px;left:33px;width:392px;height:157px" role="img" aria-label="Group of riders on horseback crossing a golden mountain valley"></div>
</section>

<!-- Hunt Details -->
<section class="page" style="top:1474px">
  <div class="photo hero tone-range" role="img" aria-label="Jagged Tian Shan mountain range above a wide valley">
    <h2 class="heading hero-title">HUNT DETAILS</h2>
  </div>
  <h3 class="label abs" style="top:233px;left:19px">HIGHLIGHTS</h3>
  <p class="abs small" style="top:250px;left:19px;width:421px">Experience an unforgettable hunting adventure in Kyrgyzstan's majestic Tian Shan Mountains. Pursue the elusive Marco Polo sheep and Siberian Ibex, hunting on horseback alongside seasoned local guides. Sharpen your long-range shooting skills, as accuracy at 400-500 meters may be required. The breathtaking scenery, from towering peaks to vast valleys, provides a stunning backdrop. This unique combination of challenging hunts and unparalleled landscapes creates a truly once-in-a-lifetime experience.</p>
  <h3 class="label abs" style="top:319px;left:19px">PROPERTY FACTS</h3>
  <p class="abs small" style="top:338px;left:19px;width:421px">Nestled deep within the majestic Tian Shan mountains, this hunting camp, a unique endeavor by the Kyrgyz government, offers an unparalleled wilderness experience. While the eight luxurious rooms each provide private bathrooms and unexpected amenities like reliable Wifi – a true rarity in such a remote setting – it's the communal spaces that truly capture the grandeur of the surroundings. The lounge area, with its striking floor-to-ceiling windows, frames breathtaking panoramic views of the rugged landscape. This blend of modern comforts and unspoiled wilderness creates a hunting retreat unlike any other.</p>
  <h3 class="label abs" style="top:419px;left:19px">GETTING THERE</h3>
  <p class="abs red" style="top:434px;left:19px;font-size:10px">Recommended Route</p>
  <p class="abs small" style="top:454px;left:19px;width:421px">International flights typically arrive at Manas International Airport (FRU) in Bishkek, Kyrgyzstan, often with layovers in Istanbul or Dubai. Upon arrival, our team will assist with firearms clearance. For guests arriving late, overnight accommodations in Bishkek can be arranged. From Bishkek, hunters have two options to reach the hunting area in the mountains: a 12-hour scenic drive or a 2.5-hour helicopter flight.</p>
  <div class="photo tone-map" style="top:506px;left:19px;width:421px;height:116px" role="img" aria-label="Map of the route from Bishkek to the mountain hunting area">
    <svg class="abs" style="left:215px;top:70px" width="14" height="20" viewBox="0 0 14 20"><path d="M7 0C3 0 0 3 0 7c0 5 7 13 7 13s7-8 7-13c0-4-3-7-7-7z" fill="var(--pin)"/><circle cx="7" cy="7" r="2.5" fill="#fff"/></svg>
  </div>
</section>

<!-- Dates & Pricing -->
<section class="page" style="top:2160px">
  <h2 class="heading abs" style="top:50px;left:35px;font-size:30px">DATES &amp; PRICING</h2>
  <h3 class="label abs red" style="top:108px;left:35px">SEASON DATES</h3>
  <p class="abs" style="top:131px;left:35px;font-size:11px">August 15th 2025 – November 30th 2025</p>
  <h3 class="label abs red" style="top:172px;left:35px">INCLUSIONS</h3>
  <p class="abs" style="top:203px;left:35px;font-size:10px">• GUIDED HUNT</p>
  <p class="abs list" style="top:228px;left:60px">7-day guided horseback hunt for Marco Polo Argali, Ibex or Both<br>Exclusive access to some of the finest hunting areas in Kyrgyzstan<br>Trophy Skinning and field preparation</p>
  <p class="abs" style="top:289px;left:35px;font-size:10px">• FOOD &amp; DRINK</p>
  <p class="abs list" style="top:312px;left:60px">Chef-prepared breakfast, packed lunch and dinner<br>A selection of non-alcoholic beverages</p>
  <p class="abs" style="top:358px;left:35px;font-size:10px">• TRAVEL &amp; LOGISTICS</p>
  <p class="abs list" style="top:385px;left:60px">Pre-arrival custom planning with the Trailmark Team<br>Round trip, fixed-time airport transfers to Bishkek</p>
  <h3 class="label abs red" style="top:442px;left:35px">PRICING</h3>
  <p class="abs list" style="top:465px;left:35px;line-height:2.05">MARCO POLO AND IBEX COMBO - $39,500 (min. 2 hunters)<br>MARCO POLO ARGALI - $32,500 (min. 2 hunters)<br>MID-ASIAN IBEX - $10,500 (Min. 2 hunters)</p>
  <h3 class="label abs red" style="top:548px;left:35px">POPULAR ADD ONS</h3>
  <p class="abs list" style="top:573px;left:35px;line-height:2.1">WOLF (Opportunistic) $2,500<br>Extra Ibex $5,500</p>
</section>

<!-- The Adventures -->
<section class="page" style="top:2856px">
  <h2 class="heading abs" style="top:32px;left:27px;font-size:28px">THE ADVENTURES</h2>
  <p class="abs" style="top:69px;left:25px;font-size:11px;line-height:1.35">A&nbsp; Stunning Camp To Revitalize Your Spirit.<br>This Is The Hunt Of A Lifetime.</p>
  <div class="photo tone-stream" style="top:106px;left:19px;width:212px;height:168px" role="img" aria-label="Riders on horseback crossing a mountain stream"></div>
  <div class="photo tone-white-horse" style="top:83px;left:246px;width:195px;height:321px" role="img" aria-label="Hunter riding a white horse up a rocky slope"></div>
  <div class="photo tone-horses-rest" style="top:287px;left:19px;width:212px;height:137px" role="img" aria-label="Horses resting beside a vehicle in a grassy valley"></div>
  <div class="photo tone-prone" style="top:443px;left:19px;width:421px;height:185px" role="img" aria-label="Hunter lying prone behind a scoped rifle on a mountain ridge">
    <p class="abs" style="top:8px;left:8px;font-size:10px;line-height:1.25">A Horseback Ride You'll Never Forget.<br>Challenging Hunts For Prized Game.</p>
  </div>
</section>

<!-- The Lodge -->
<section class="page" style="top:3541px">
  <h2 class="heading abs" style="top:32px;left:25px;font-size:28px">THE LODGE</h2>
  <div class="photo tone-lounge" style="top:75px;left:25px;width:222px;height:141px" role="img" aria-label="Wood-panelled lodge lounge with mounted trophies">
    <p class="abs caption" style="top:70px;left:5px;width:212px">Beyond The Reach Of Ordinary Travel Lies A Hidden World Of Spectacular Beauty And Unrivaled Hunting.</p>
  </div>
  <div class="photo tone-sitting" style="top:37px;left:262px;width:174px;height:325px" role="img" aria-label="Log-walled sitting room with white sofas and wildlife painting"></div>
  <div class="photo tone-dining" style="top:226px;left:25px;width:222px;height:145px" role="img" aria-label="Lodge dining area with carpets and leather chairs">
    <p class="abs caption" style="top:6px;left:5px;width:200px;font-size:9px">Our Kyrgyzstan Experience Is Crafted For The Discerning Sportsman, Offering Access To Pristine Wilderness And Luxurious Accommodations. This Is Hunting Elevated To An Art Form.</p>
  </div>
  <div class="photo tone-billiards" style="top:381px;left:29px;width:214px;height:245px" role="img" aria-label="Games room with a teal billiard table under hanging lamps"></div>
  <div class="photo tone-corridor" style="top:381px;left:258px;width:178px;height:245px" role="img" aria-label="Long wooden corridor with guest room doors"></div>
</section>

<!-- Back cover -->
<section class="page" style="top:4237px">
  <p class="abs brand-name" style="top:150px;left:0;width:100%;text-align:center;font-size:18px">TRAILMARK</p>
  <p class="abs brand-name" style="top:318px;left:0;width:100%;text-align:center;font-size:18px">RIDGELINE WORKS</p>
  <p class="abs" style="top:574px;left:0;width:100%;text-align:center;font-size:10px;line-height:1.9">+961 555 0142<br>www.trailmarkhunts.com<br>bookings@trailmarkhunts.com</p>
</section>

</body>
</html>
```